Digital Recipe eBook Design

I need a recipe eBook designed for me. I have attached the recipes (see here https://pages.tarnovel.net/sheet/k/7Qp3XZ41TTb82Lr5mkdBvxhpJQ0NsoRPYcEAK63FXwtu/view?mode=public) and associated images in Google Drive (see images here https://store.plumvexa.com/store/bundles/83KTsQwund5Ho2Pcm6yvbrEXk0TZ?mode=public). I am open to any sort of ideas but want the recipe book to look highly professional and with a simple, yet sleek, design. I have included some examples of designs I like here: https://store.plumvexa.com/store/bundles/6R_Ty4GDqJpsm-NnbwuhLoEC0PZBk?mode=public

Target Market(s)

Women 20-35

Industry/Entity Type

Health And Wellness

Font styles to use
Sans Serif

Colors
e667a6
eea4c8
f9deeb

Requirements
Must have
• No typos
• Professional design
Should not have
• Overly decorative design - keep it simple and clean

```html
<!DOCTYPE html>
<html lang="en">
<head>
<meta charset="utf-8">
<title>The Calm Cycle Cookbook – Page Spreads</title>
<link rel="stylesheet" href="https://fonts.googleapis.com/css2?family=Jost:wght@300;400&family=Montserrat:ital,wght@0,400;0,600;0,700;1,400&display=swap">
<style>
:root{
  --pink:#e667a6;
  --pink-mid:#eea4c8;
  --pink-soft:#f9deeb;
  --board:#b3b3b3;
  --paper:#ffffff;
  --ink:#555555;
  --ink-soft:#777777;
}
*{box-sizing:border-box;margin:0;padding:0}
html,body{width:1200px;height:675px;overflow:hidden;background:var(--board)}
body{position:relative;font-family:"Montserrat",sans-serif;color:var(--ink)}
.page{position:absolute;width:209px;height:270px;background:var(--paper);overflow:hidden;box-shadow:0 1px 3px rgba(0,0,0,.18)}
.page::after{content:"";position:absolute;left:0;right:0;bottom:0;height:6px;background:var(--pink-mid)}
.page.no-band::after{display:none}
.photo{position:absolute}
.ph-bowl{background:linear-gradient(135deg,#5f7f3a,#e8e2c6 45%,#c9b84a 70%,#d9682f)}
.ph-dessert{background:linear-gradient(135deg,#6f4a36,#b8906e 60%,#e3d7c6)}
.ph-bars{background:linear-gradient(135deg,#8a6a45,#c7ad84 55%,#eee6da)}
.ph-bread{background:linear-gradient(135deg,#7b5a3a,#d8c2a0)}
.ph-balls{background:linear-gradient(135deg,#f0eee9,#7a4e34 60%,#4a2e22)}
.ph-muffins{background:linear-gradient(135deg,#5d5d5d,#d6a24a 40%,#c7552e 65%,#6a6a6a)}
.ph-smoothie{background:linear-gradient(160deg,#e8e6e2,#c7a08a 45%,#6f4a3b)}
.ph-green{background:linear-gradient(160deg,#c9c5d6,#6fae2c 55%,#4a7d1f)}

/* cover */
.cover-title{position:absolute;top:31px;left:0;right:0;text-align:center;color:var(--pink);font-weight:600;font-size:11px;letter-spacing:4px;line-height:15px}
.cover-grid{position:absolute;left:27px;top:83px;width:155px;height:139px}
.cover-grid .photo{width:76px;height:68px}
.cover-badge{position:absolute;left:61px;top:108px;width:88px;height:88px;border-radius:50%;background:var(--pink-mid);color:#fff;font-family:"Jost",sans-serif;font-weight:300;font-size:11px;line-height:16px;display:flex;align-items:center;justify-content:center;text-align:center}
.cover-band{position:absolute;left:0;right:0;bottom:0;height:17px;background:var(--pink-mid);color:#fff;font-size:7px;font-weight:600;letter-spacing:2px;text-align:center;line-height:17px;z-index:2}

/* text pages */
.page-heading{position:absolute;font-family:"Jost",sans-serif;font-weight:300;color:var(--pink);font-size:10px}
.welcome-body{position:absolute;left:27px;top:83px;width:158px;font-size:3.5px;line-height:5.4px;color:#333}
.welcome-body p{margin-bottom:5px}

/* contents */
.top-band{position:absolute;left:0;right:0;top:0;height:6px;background:var(--pink-mid)}
.toc-spine{position:absolute;left:14px;top:37px;width:28px;height:193px;background:var(--pink-mid);display:flex;align-items:center;justify-content:center}
.toc-spine span{transform:rotate(-90deg);white-space:nowrap;color:#fff;font-weight:700;font-size:13px;letter-spacing:1.5px}
.toc-mark{position:absolute;left:54px;top:38px;width:13px;height:3px;background:var(--pink-mid)}
.toc{position:absolute;left:54px;top:45px;width:125px}
.toc h3{font-size:4.2px;font-weight:600;letter-spacing:.4px;color:#444;margin:5px 0 2px}
.toc li{list-style:none;display:flex;justify-content:space-between;font-style:italic;font-size:3.4px;line-height:7px;color:#555}
.toc li b{font-weight:400;font-style:normal}

/* section divider */
.divider-grid{position:absolute;left:27px;top:62px;width:155px;height:139px}
.divider-grid .photo{width:76px;height:68px}
.divider-label{position:absolute;left:54px;top:113px;width:101px;height:26px;background:var(--pink-mid);border:1px solid #fff;color:#fff;font-family:"Jost",sans-serif;font-weight:300;font-size:19px;line-height:24px;text-align:center}

/* recipe pages */
.recipe-title{position:absolute;left:14px;top:16px;font-family:"Jost",sans-serif;font-weight:300;color:var(--pink);font-size:9px}
.sub-heading{font-family:"Jost",sans-serif;font-weight:300;color:var(--pink);font-size:9px;margin-bottom:3px}
.ingredients{position:absolute;width:72px;font-size:4px;line-height:7.4px;letter-spacing:.2px;color:#666}
.ingredients ul{padding-left:5px}
.serves{position:absolute;font-size:3.6px;color:var(--pink-mid)}
.method{position:absolute;font-size:3.7px;line-height:6.6px;color:#666}
.method ol{padding-left:4px;margin-top:8px}
.method .note{color:var(--pink);margin-top:5px}

/* overlay captions */
.caption{position:absolute;background:rgba(230,103,166,.62);color:#fff;font-size:3.7px;line-height:5.4px;padding:4px 5px;text-align:justify}
.caption ul{padding-left:5px;margin:3px 0}
</style>
</head>
<body>

<!-- Row 1 -->
<section class="page cover" style="left:42px;top:61px">
  <h1 class="cover-title">The<br>Calm Cycle<br>Cookbook</h1>
  <div class="cover-grid">
    <div class="photo ph-dessert" style="left:0;top:0" role="img" aria-label="Chocolate chia puddings with berries"></div>
    <div class="photo ph-bars" style="left:79px;top:0" role="img" aria-label="Seed bars on baking paper"></div>
    <div class="photo ph-bread" style="left:0;top:71px" role="img" aria-label="Sliced seeded loaf"></div>
    <div class="photo ph-balls" style="left:79px;top:71px" role="img" aria-label="Chocolate bliss balls in a bowl"></div>
  </div>
  <div class="cover-badge">Bloom<br>Balance<br>Wellness</div>
  <div class="cover-band">by Tess Marlow</div>
</section>

<section class="page welcome" style="left:269px;top:61px">
  <h2 class="page-heading" style="left:27px;top:46px">Welcome</h2>
  <div class="welcome-body">
    <p><i>Food is foundational when it comes to hormone balance.</i> What you eat directly contributes to how well your body creates new hormones, detoxifies used-up hormones and how regularly you ovulate.</p>
    <p>As you learn the importance of certain cycle-supporting foods in the Cycle Sync Studio modules, it can feel overwhelming if you haven't included these foods in your diet before.</p>
    <p>The aim of this cookbook is to take away the overwhelm and get you excited about the possibilities of eating these foods.</p>
    <p>I'm sharing with you simple and delicious ways to prepare these cycle-supporting ingredients, along with lots of tips and tricks to individualise each recipe.</p>
    <p>All of the recipes included in this cookbook are gluten free, dairy free and offer vegetarian alternatives. Once you are comfortable with these recipes, feel free to experiment with them by subbing in and out different ingredients such as the vegetables or proteins suggested. The sky is the limit!</p>
    <p><b>I would love to see what you create!</b> Tag me on Instagram @bloombalancewellness or post in our Bloomers Circle group when you make any of the recipes.</p>
    <p>Happy cooking!</p>
    <p>Tess.</p>
  </div>
</section>

<section class="page contents" style="left:499px;top:61px">
  <div class="top-band"></div>
  <div class="toc-spine"><span>TABLE OF CONTENTS</span></div>
  <div class="toc-mark"></div>
  <div class="toc">
    <h3>BREAKFAST</h3>
    <ul>
      <li>The Goddess Breakfast Bowl<b>5</b></li>
      <li>Meal-Prep Egg Muffins<b>7</b></li>
      <li>Chocolate Cauliflower Smoothie<b>9</b></li>
      <li>Green Detox Smoothie<b>11</b></li>
      <li>Buckwheat Porridge with Stewed Rhubarb<b>13</b></li>
    </ul>
    <h3>MAINS</h3>
    <ul>
      <li>Miso-Tahini Poke Bowl/Crispy<b>16</b></li>
      <li>Chickpea and Kale Salad<b>18</b></li>
      <li>The Simplest Gluten Free Buckwheat Bread<b>19</b></li>
      <li>Mexican Burrito Bowls<b>20</b></li>
      <li>One-Pan Salmon Pesto<b>21</b></li>
      <li>Antipasto Salad<b>22</b></li>
    </ul>
    <h3>SNACKS</h3>
    <ul>
      <li>Miso-Tahini Poke Bowl<b>23</b></li>
      <li>Crispy Chickpea and Kale Salad<b>24</b></li>
      <li>The Simplest Gluten Free Buckwheat Bread<b>25</b></li>
      <li>Mexican Burrito Bowls<b>26</b></li>
      <li>One-Pan Salmon Pesto<b>27</b></li>
      <li>Antipasto Salad<b>28</b></li>
    </ul>
    <h3>DRINKS</h3>
    <ul>
      <li>Descriptive Statistics<b>30</b></li>
      <li>Factor Analysis<b>31</b></li>
    </ul>
  </div>
</section>

<section class="page divider" style="left:728px;top:61px">
  <div class="divider-grid">
    <div class="photo ph-bowl" style="left:0;top:0" role="img" aria-label="Goddess breakfast bowl"></div>
    <div class="photo ph-smoothie" style="left:79px;top:0" role="img" aria-label="Chocolate smoothie in a glass"></div>
    <div class="photo ph-muffins" style="left:0;top:71px" role="img" aria-label="Egg muffins on a cooling rack"></div>
    <div class="photo ph-green" style="left:79px;top:71px" role="img" aria-label="Green smoothies in bottles"></div>
  </div>
  <div class="divider-label">Breakfast</div>
</section>

<section class="page recipe" style="left:956px;top:61px">
  <h2 class="recipe-title">Goddess Breakfast Bowl</h2>
  <div class="photo ph-bowl" style="left:18px;top:47px;width:83px;height:54px" role="img" aria-label="Breakfast bowl with eggs, avocado, cauliflower and sweet potato"></div>
  <div class="serves" style="left:18px;top:105px">Serves 1</div>
  <div class="ingredients" style="left:113px;top:41px">
    <h3 class="sub-heading">Ingredients</h3>
    <ul>
      <li>2 eggs (free range or organic where possible)</li>
      <li>¼ avocado</li>
      <li>½ small sweet potato, cubed (around ½ cup)</li>
      <li>2 florets of cauliflower</li>
      <li>Large handful of fresh greens (e.g. baby spinach)</li>
      <li>Drizzle of olive oil</li>
    </ul>
  </div>
  <div class="method" style="left:18px;top:139px;width:176px">
    <h3 class="sub-heading">How To:</h3>
    <ol>
      <li>Boil a small saucepan of water and gently add the two eggs; set a timer for 6 minutes (soft) or 10 minutes (hard).</li>
      <li>Meanwhile, steam the sweet potato and cauliflower until just soft.</li>
      <li>When the eggs are done, move them to an ice-cold bowl of water for 2-3 minutes.</li>
      <li>Remove the eggs from the water and peel away their shells.</li>
      <li>Assemble: greens at the bottom, topped with eggs, sweet potato, cauliflower and avocado.</li>
      <li>Garnish with salt and pepper and a drizzle of olive oil.</li>
      <li>Enjoy!</li>
    </ol>
  </div>
</section>

<!-- Row 2 -->
<section class="page no-band" style="left:42px;top:357px">
  <div class="photo ph-bowl" style="inset:0" role="img" aria-label="Close-up of the goddess breakfast bowl"></div>
  <div class="caption" style="left:21px;top:177px;width:172px">
    This bowl is the ultimate balanced breakfast for your hormones that will keep you full all morning. Start your day by ticking all the hormone-balancing principles in one bowl:
    <ul>
      <li>Healthy fats from avocado, egg yolks and olive oil</li>
      <li>Protein from eggs</li>
      <li>Complex carbohydrates from sweet potato</li>
      <li>Liver and cycle-supporting nutrients from cauliflower and greens</li>
    </ul>
    NOTE: This bowl can be prepared the night before for an easy grab-and-go breakfast.
  </div>
</section>

<section class="page recipe" style="left:269px;top:357px">
  <h2 class="recipe-title" style="left:17px">Meal Prep Egg Muffins</h2>
  <div class="photo ph-muffins" style="left:18px;top:47px;width:83px;height:54px" role="img" aria-label="Egg muffins on a cooling rack"></div>
  <div class="serves" style="left:18px;top:106px">Makes around 12 muffins</div>
  <div class="ingredients" style="left:113px;top:41px">
    <h3 class="sub-heading">Ingredients</h3>
    <ul>
      <li>1 cup chopped broccoli</li>
      <li>2 Tablespoons chopped onions</li>
      <li>1/4 cup chopped red capsicum</li>
      <li>8 eggs, whisked</li>
      <li>1/2 cup (120 ml) coconut milk</li>
      <li>Salt and pepper to taste</li>
    </ul>
  </div>
  <div class="method" style="left:17px;top:129px;width:176px">
    <h3 class="sub-heading">How To:</h3>
    <ol>
      <li>Preheat oven to 180°C (350°F).</li>
      <li>Mix the vegetables, whisked eggs and coconut milk together in a large mixing bowl.</li>
      <li>Pour batter into muffin cups (an average sized 12-capacity tray should fit the mixture).</li>
      <li>Bake for 25-30 minutes until the middle of the muffins are solid when touched.</li>
      <li>Serve as is for an on-the-go breakfast or snack, or serve with a piece of toast and some avocado for a more filling breakfast.</li>
    </ol>
    <p class="note">Mix up the flavours:</p>
    <p class="note" style="margin-top:2px">You can use any variety of chopped vegetables that you like. Get creative and add extra flavour with smoked salmon, crumbled feta, fresh herbs such as basil, dried herbs and spices, roasted sweet potato or a spoon of pesto in each muffin tin.</p>
  </div>
</section>

<section class="page no-band" style="left:499px;top:357px">
  <div class="photo ph-muffins" style="inset:0" role="img" aria-label="Egg muffins cooling on a wire rack"></div>
  <div class="caption" style="left:14px;top:207px;width:181px">
    These high protein muffins are a perfect Sunday meal prep recipe to get yourself set up for a week of healthy breakfast. Mix and match the filling ingredients with your favourite vegetables and proteins. Once cooked you can cool down and store portioned in the fridge for super simple on-the-go breakfasts or snacks throughout the day.
  </div>
</section>

<section class="page recipe" style="left:728px;top:357px">
  <h2 class="recipe-title">Chocolate Cauliflower Smoothie</h2>
  <div class="photo ph-smoothie" style="left:18px;top:70px;width:78px;height:64px" role="img" aria-label="Hand holding a chocolate smoothie"></div>
  <div class="serves" style="left:18px;top:143px">Serves 1</div>
  <div class="ingredients" style="left:113px;top:41px">
    <h3 class="sub-heading">Ingredients</h3>
    <ul>
      <li>¾ cup steamed cauliflower (cooled in the fridge) TIP: make a batch of cauliflower on the weekend for easy breakfasts</li>
      <li>1 banana, cut into chunks and frozen</li>
      <li>⅓ avocado</li>
      <li>½ cup coconut or almond milk</li>
      <li>2 Tbsp cacao powder</li>
      <li>1 scoop protein powder (I recommend vanilla or chocolate flavoured)</li>
    </ul>
  </div>
  <div class="method" style="left:20px;top:181px;width:172px">
    <h3 class="sub-heading">How To:</h3>
    <ol>
      <li>Add all ingredients to a blender or food processor and blend until smooth. Enjoy straight away or store in the fridge for up to 1 day.</li>
      <li>TIP: this recipe makes a thick smoothie that can be eaten with a spoon. For a thinner smoothie, increase the milk to around 1 cup.</li>
    </ol>
  </div>
</section>

<section class="page no-band" style="left:956px;top:357px">
  <div class="photo ph-smoothie" style="inset:0" role="img" aria-label="Glass of chocolate smoothie topped with cacao nibs"></div>
  <div class="caption" style="left:10px;top:163px;width:190px">
    Don't be put off by the cauliflower! This rich chocolatey smoothie tastes like a decadent dessert, but secretly includes a liver-supporting dose of cauliflower that you truly cannot taste. The avocado in this smoothie makes it smooth and creamy, plus supplies your body with healthy fats to create your hormones. Combining healthy fats from avocado, sweetness from bananas and protein powder to keep you full all morning, this smoothie meets all the hormone-balancing principles. Cauliflower is one of the best foods you can eat to support your liver's detoxification of excess hormones - helping you maintain balanced hormone levels.
  </div>
</section>

</body>
</html>
```